Income Tax and Accounting Brochure

I need a brochure using my new logo (file attached). I do tax work and accounting work. I am an EA (QFB Enrolled Agent - logo attached) and would like this incorporated into the brochure. I also have a MSA in Accounting. Please incorporate the text that I have provided in the brochure.
Updates

Need extra days to review

Target Market(s)

Tax Clients - both business and individuals

Industry/Entity Type

Accounting

Colors
0054AA
0677BA
7BADD7
CADEEF
E8F1F8

Requirements
Must have
• Use my logo and the QFB EA file in the brochure
Nice to have
• I would like to see a brochure that I can customize with my own text if possible.

```html
<!DOCTYPE html>
<html lang="en">
<head>
<meta charset="utf-8">
<title>Keystone Ledger &amp; Advisory – Brochure</title>
<link href="https://fonts.googleapis.com/css2?family=Montserrat:wght@400;500;600;700&family=Open+Sans:ital,wght@0,300;0,400;0,600;0,700;1,600;1,700&display=swap" rel="stylesheet">
<style>
  :root{
    --blue:#0054AA;
    --blue-mid:#0677BA;
    --blue-light:#7BADD7;
    --blue-pale:#CADEEF;
    --blue-mist:#E8F1F8;
    --red:#C8102E;
    --ink:#4a4f57;
    --paper:#ffffff;
    --paper-grey:#eef0f3;
    --stage:#959595;
    --head:'Montserrat',sans-serif;
    --body:'Open Sans',sans-serif;
  }
  *{box-sizing:border-box;margin:0;padding:0}
  html,body{width:1200px;height:2232px;overflow:hidden;background:var(--stage)}
  .canvas{position:relative;width:1200px;height:2232px;overflow:hidden;background:var(--stage);font-family:var(--body);color:var(--ink)}
  .page-label{position:absolute;top:272px;width:540px;text-align:center;font-family:var(--body);font-weight:300;font-size:21px;color:#fff}
  .page{position:absolute;top:320px;width:540px;height:721px;overflow:hidden;background:var(--paper);box-shadow:0 2px 8px rgba(0,0,0,.35)}
  .page svg.art{position:absolute;inset:0}
  .cover{left:40px}
  .back{left:620px;background:linear-gradient(160deg,#ffffff 0%,#f1f2f4 60%,#e6e8eb 100%)}

  /* cover brand */
  .brand{position:absolute;left:160px;top:526px;display:flex;align-items:center;gap:14px}
  .brand-mark{width:64px;height:64px;border-radius:50%;background:var(--blue);flex:none}
  .brand-name{font-family:var(--head);font-weight:600;color:var(--blue);font-size:19px;line-height:1.3;letter-spacing:.06em}
  .brand-url{position:absolute;left:238px;top:600px;font-family:var(--head);font-weight:600;color:var(--blue);font-size:14px;letter-spacing:.08em}

  /* back page */
  .band{position:absolute;background:var(--blue);color:#fff;font-family:var(--head);font-weight:600;border-radius:0 10px 10px 0}
  .back .band.title{left:0;top:60px;width:465px;height:24px;font-size:15px;text-align:center;line-height:24px}
  .back .intro{position:absolute;left:37px;top:87px;width:428px;font-size:12.5px;line-height:1.36;color:var(--ink)}
  .services{position:absolute;left:30px;top:200px;display:flex;gap:36px}
  .service{width:96px;text-align:center;font-size:12.5px;line-height:1.3;color:var(--ink)}
  .service .disc{width:62px;height:62px;margin:0 auto 12px;border-radius:50%;background:radial-gradient(circle,#fff 48%,var(--blue-pale) 50%,#d9e2ec 100%);display:flex;align-items:center;justify-content:center}
  .cta{position:absolute;left:32px;top:358px;width:308px;height:34px;border-radius:8px;background:var(--blue);color:#fff;font-family:var(--head);font-size:13px;line-height:34px;padding-left:12px;letter-spacing:.02em}
  .cta b{font-weight:700}
  .contacts{position:absolute;left:36px;top:408px;list-style:none}
  .contacts li{display:flex;align-items:center;gap:18px;font-family:var(--head);font-size:13.5px;color:#333;height:36px}
  .contacts .ico{width:30px;height:30px;border-radius:50%;background:#8a8f96;display:flex;align-items:center;justify-content:center;flex:none}

  /* inner spread */
  .spread{position:absolute;left:40px;top:1120px;width:1120px;height:806px;overflow:hidden;background:var(--paper);box-shadow:0 2px 8px rgba(0,0,0,.35)}
  .spread .right-panel{position:absolute;left:540px;top:0;width:580px;height:806px;background:linear-gradient(180deg,#f5f6f8,var(--paper-grey))}
  .spread svg.decor{position:absolute;left:0;top:0}
  .about-word{position:absolute;left:152px;top:20px;font-family:var(--body);font-weight:700;font-size:54px;line-height:1;color:#d0d3d8;letter-spacing:-.01em}
  .spread .band{height:26px;line-height:26px;font-size:16px;text-align:center;width:500px;left:0}
  .band.principal{top:78px}
  .band.why{top:396px;font-style:italic;font-family:var(--body);font-weight:700}
  .copy{position:absolute;font-size:13px;line-height:1.44;font-weight:300;color:#3c4047;text-align:justify}
  .copy p+p{margin-top:18px}
  .agent-badge{position:absolute;left:150px;top:224px;width:216px;height:50px;border:2px solid var(--blue);background:#fff;display:flex;gap:4px;padding:4px}
  .agent-badge span{display:block}
  .agent-badge .a{width:88px;background:#cfcfcf;border:2px solid #8d7b43}
  .agent-badge .b{flex:1;background:#e2e3e5}
  .benefits{position:absolute;left:585px;top:38px;width:490px;height:440px;border:2px solid #c8ccd2}
  .benefits-tab{position:absolute;left:700px;top:26px;width:265px;height:27px;line-height:27px;background:var(--blue);color:#fff;font-family:var(--head);font-weight:600;font-size:15.5px;text-align:center;border-radius:8px 8px 0 0}
  .benefit{position:absolute;left:635px;display:flex;align-items:center}
  .benefit .ring{width:58px;height:58px;flex:none}
  .benefit .rule{width:1px;height:66px;background:var(--blue);margin:0 22px 0 24px}
  .benefit p{width:312px;font-size:13px;line-height:1.44;font-weight:300;color:#3c4047;text-align:justify}
  .mess-title{position:absolute;left:586px;top:500px;font-family:var(--body);font-weight:700;font-size:21px;color:var(--red)}
  .mess-copy{left:586px;top:534px;width:330px;font-size:12.5px;text-align:justify}
  .tagline{position:absolute;left:30px;top:756px;font-family:var(--body);font-weight:700;font-style:italic;font-size:19px;color:#fff}
  .spread-url{position:absolute;right:18px;top:758px;font-family:var(--body);font-weight:400;font-size:16px;color:#fff;letter-spacing:.08em}
</style>
</head>
<body>
<main class="canvas">

  <div class="page-label" style="left:40px">Cover Page</div>
  <div class="page-label" style="left:620px">Back Page</div>

  <!-- Cover -->
  <section class="page cover">
    <svg class="art" width="540" height="721" viewBox="0 0 540 721">
      <defs>
        <linearGradient id="coverPhoto" x1="0" y1="0" x2="1" y2="1">
          <stop offset="0" stop-color="#e9ebee"/>
          <stop offset=".45" stop-color="#b7c0ca"/>
          <stop offset=".75" stop-color="#6b7480"/>
          <stop offset="1" stop-color="#3d4550"/>
        </linearGradient>
        <clipPath id="coverCircle"><circle cx="335" cy="185" r="290"/></clipPath>
      </defs>
      <rect width="540" height="721" fill="var(--blue)"/>
      <path d="M0,0 H540 V640 Q300,700 0,625 Z" fill="#fff"/>
      <circle cx="335" cy="185" r="300" fill="none" stroke="var(--blue)" stroke-width="22"/>
      <g clip-path="url(#coverCircle)">
        <rect x="0" y="0" width="540" height="480" fill="url(#coverPhoto)" role="img" aria-label="Photo of hands working a calculator over financial papers"/>
        <path d="M170,480 L290,120 L330,130 L225,480 Z" fill="var(--red)" opacity=".75"/>
        <path d="M20,280 Q220,70 520,190" fill="none" stroke="var(--blue-light)" stroke-width="30" opacity=".45"/>
      </g>
      <path d="M0,660 Q300,672 540,666" fill="none" stroke="var(--red)" stroke-width="7"/>
      <path d="M0,678 Q300,688 540,684" fill="none" stroke="#fff" stroke-width="5"/>
    </svg>
    <div class="brand">
      <span class="brand-mark"></span>
      <span class="brand-name">KEYSTONE LEDGER<br>&amp; ADVISORY, LLC</span>
    </div>
    <div class="brand-url">WWW.KEYSTONELEDGER.COM</div>
  </section>

  <!-- Back -->
  <section class="page back">
    <svg class="art" width="540" height="721" viewBox="0 0 540 721">
      <path d="M540,120 Q500,300 540,520 Z" fill="var(--blue)"/>
      <path d="M0,590 Q300,560 540,495 V721 H0 Z" fill="var(--blue)"/>
      <path d="M0,600 Q300,570 540,500" fill="none" stroke="var(--red)" stroke-width="14"/>
      <path d="M0,618 Q300,588 540,522" fill="none" stroke="#fff" stroke-width="5"/>
    </svg>
    <div class="band title">KEYSTONE LEDGER &amp; ADVISORY, LLC</div>
    <p class="intro">If you are looking for a blend of personal service and expertise, you have come to the right place! We offer a broad range of services for business owners, executives and independent professionals. Our rates are affordable. We are experienced and friendly.</p>
    <div class="services">
      <div class="service"><div class="disc">
        <svg width="30" height="24" viewBox="0 0 30 24"><path d="M1,3 H11 L14,6 H29 V23 H1 Z" fill="var(--blue)"/></svg>
      </div>TAX SERVICES</div>
      <div class="service"><div class="disc">
        <svg width="30" height="30" viewBox="0 0 30 30"><circle cx="15" cy="15" r="13" fill="var(--blue)"/><path d="M8,9 Q12,7 14,11 Q11,15 9,13 Z M17,16 Q22,15 22,20 Q19,24 17,20 Z" fill="#fff"/></svg>
      </div>BUSINESS<br>SERVICES</div>
      <div class="service"><div class="disc">
        <svg width="32" height="28" viewBox="0 0 32 28"><path d="M16,2 L31,15 H27 V27 H19 V19 H13 V27 H5 V15 H1 Z" fill="var(--blue)"/></svg>
      </div>SERVICES FOR<br>INDIVIDUALS</div>
    </div>
    <div class="cta">CONTACT US FOR A <b>FREE CONSULTATION</b></div>
    <ul class="contacts">
      <li style="height:48px"><span class="ico"><svg width="14" height="18" viewBox="0 0 14 18"><path d="M7,1 A6,6 0 0 1 13,7 C13,11 7,17 7,17 C7,17 1,11 1,7 A6,6 0 0 1 7,1 Z" fill="#fff"/><circle cx="7" cy="7" r="2.3" fill="#8a8f96"/></svg></span><span>2870 Orchard Hollow Rd<br>Fairmont, VA 20190</span></li>
      <li><span class="ico"><svg width="16" height="12" viewBox="0 0 16 12"><rect x="1" y="1" width="14" height="10" fill="#fff"/><path d="M1,1 L8,7 L15,1" fill="none" stroke="#8a8f96" stroke-width="1.3"/></svg></span>info@keystoneledger.com</li>
      <li><span class="ico"><svg width="16" height="16" viewBox="0 0 16 16"><path d="M3,1 L6,1 L7,5 L5,6.5 Q6.5,9.5 9.5,11 L11,9 L15,10 L15,13 Q14,15 12,15 Q3,13 1,4 Q1,2 3,1 Z" fill="#fff"/></svg></span>(555)014-2278</li>
      <li><span class="ico"><svg width="16" height="14" viewBox="0 0 16 14"><rect x="1" y="4" width="14" height="9" fill="#fff"/><rect x="4" y="1" width="8" height="4" fill="#fff"/><rect x="4" y="7" width="8" height="1.5" fill="#8a8f96"/><rect x="4" y="10" width="8" height="1.5" fill="#8a8f96"/></svg></span>(555) 017-3390</li>
    </ul>
  </section>

  <!-- Inner spread -->
  <section class="spread">
    <div class="right-panel"></div>

    <svg class="decor" width="1120" height="806" viewBox="0 0 1120 806">
      <defs>
        <linearGradient id="deskPhoto" x1="0" y1="0" x2="1" y2="1">
          <stop offset="0" stop-color="#f1f2f4"/>
          <stop offset=".6" stop-color="#a9b3be"/>
          <stop offset="1" stop-color="#5d6672"/>
        </linearGradient>
      </defs>
      <path d="M0,690 Q520,735 1120,690 V806 H0 Z" fill="var(--blue)"/>
      <path d="M0,672 Q520,718 1120,676" fill="none" stroke="var(--red)" stroke-width="9"/>
      <path d="M0,688 Q520,730 1120,690" fill="none" stroke="#fff" stroke-width="5"/>
      <circle cx="1030" cy="618" r="82" fill="var(--blue)"/>
      <circle cx="1030" cy="618" r="75" fill="url(#deskPhoto)" role="img" aria-label="Photo of hands writing on a financial report at a desk"/>
    </svg>

    <div class="about-word">ABOUT</div>
    <div class="band principal">MARIAN T HOLLOWAY, MSA EA (PRINCIPAL)</div>
    <div class="copy" style="left:30px;top:110px;width:474px">
      <p>I have a Masters' Degree in accounting and am an QFB Enrolled Agent. I am also a TallyPoint Advanced Certified Consultant in both the online and desktop products including Enterprise and Point of Sale. I provide individual and small business tax services, Accounting, bookkeeping, QFB representation, insurance audit representation, business license assistance and more.</p>
    </div>
    <div class="agent-badge" role="img" aria-label="Enrolled agent credential badge"><span class="a"></span><span class="b"></span></div>
    <div class="copy" style="left:30px;top:290px;width:474px">
      <p>I have experience working with a wide variety of clients from the point where they first decide they want to start a business. They are often unsure about what to do first- I have a lot of experience to offer you.</p>
    </div>

    <div class="band why">TAX PREPARATION – WHY HIRE US?</div>
    <div class="copy" style="left:30px;top:436px;width:474px">
      <p>Preparing your own income tax return can be a task that leaves you with more questions than answers. According to a study released by the National Audit Bureau last year, most taxpayers (77% of 71 million taxpayers) believe they benefited from using a professional tax preparer.</p>
      <p>Whether we like it or not, today's tax laws are so complicated that filing a relatively simple return can be confusing. It is just too easy to overlook deductions and credits to which you are entitled. Even if you use a computer software program there's no substitute for the assistance of an experienced tax professional.</p>
    </div>

    <div class="benefits"></div>
    <div class="benefits-tab">HERE'S WHAT YOUR GET...</div>

    <div class="benefit" style="top:82px">
      <svg class="ring" viewBox="0 0 58 58"><circle cx="29" cy="29" r="27" fill="#fff" stroke="var(--blue-pale)" stroke-width="2"/><path d="M29,2 A27,27 0 0 1 56,29" fill="none" stroke="var(--blue)" stroke-width="3"/><circle cx="26" cy="26" r="9" fill="none" stroke="var(--blue)" stroke-width="2.5"/><path d="M32.5,32.5 L41,41" stroke="var(--blue)" stroke-width="3.5"/></svg>
      <span class="rule"></span>
      <p>Your tax return will be checked and rechecked by our computer software identifying potential problems the QFB may look at more closely and reviewing the math to limit QFB contacts.</p>
    </div>
    <div class="benefit" style="top:184px">
      <svg class="ring" viewBox="0 0 58 58"><circle cx="29" cy="29" r="27" fill="#fff" stroke="var(--blue-pale)" stroke-width="2"/><path d="M29,2 A27,27 0 0 1 56,29" fill="none" stroke="var(--blue)" stroke-width="3"/><rect x="19" y="16" width="20" height="26" fill="none" stroke="var(--blue)" stroke-width="2"/><path d="M23,23 H35 M23,28 H35 M23,33 H31" stroke="var(--blue)" stroke-width="2"/></svg>
      <span class="rule"></span>
      <p>Your tax return can be filed electronically so you will get a refund back quicker.</p>
    </div>
    <div class="benefit" style="top:280px">
      <svg class="ring" viewBox="0 0 58 58"><circle cx="29" cy="29" r="27" fill="#fff" stroke="var(--blue-pale)" stroke-width="2"/><path d="M29,2 A27,27 0 0 1 56,29" fill="none" stroke="var(--blue)" stroke-width="3"/><circle cx="22" cy="30" r="6" fill="none" stroke="var(--blue)" stroke-width="2"/><path d="M30,40 V34 M35,40 V29 M40,40 V23" stroke="var(--blue)" stroke-width="3"/><path d="M28,27 L40,17" stroke="var(--blue)" stroke-width="2"/></svg>
      <span class="rule"></span>
      <p>Our staff will show you how to adjust your payroll withholding to get more money back each week. Why give the QFB an interest free loan for up to 16 months.</p>
    </div>
    <div class="benefit" style="top:380px">
      <svg class="ring" viewBox="0 0 58 58"><circle cx="29" cy="29" r="27" fill="#fff" stroke="var(--blue-pale)" stroke-width="2"/><path d="M29,2 A27,27 0 0 1 56,29" fill="none" stroke="var(--blue)" stroke-width="3"/><path d="M29,14 L41,19 V28 Q41,38 29,44 Q17,38 17,28 V19 Z" fill="none" stroke="var(--blue)" stroke-width="2.5"/><path d="M23,29 L28,34 L36,24" fill="none" stroke="var(--blue)" stroke-width="2.5"/></svg>
      <span class="rule"></span>
      <p>We will show you potential deductions to limit your tax liability for next year. In addition, we will give you a sheet of commonly overlooked deductions to limit the following year's tax liability.</p>
    </div>

    <div class="mess-title">BOOKS A MESS: NO PROBLEM!</div>
    <div class="copy mess-copy">If you own a small business and haven't kept up your bookkeeping, don't worry. We can help you. We'll prepare your bookkeeping for the year, prepare a full Schedule C, as well as your personal income tax return. Then we'll help you set up an easy system that allows you to keep your books in tip-top shape next year.</div>

    <div class="tagline">WHAT A JOY IT IS TO WATCH SUCCESS IN ACTION!</div>
    <div class="spread-url">WWW.KEYSTONELEDGER.COM</div>
  </section>

</main>
</body>
</html>
```